brightwell - Property Management DL Card

I am after a savvy designer to cut through junk mail! so many real estate agents use flyers to promote themselves and their business and usually sales. We are a property management firm (residential) and we want to represent landlords that have existing investment properties and need a quality agent to represent them. Can you help?
DL size, will be printed and delivered to mailboxes. For a look at our website go to www.brightwellrs.com.au. Keep it simple and clutter free.
it is to be double sided - with one side to be simple and clear - just our website, logo and telephone number on the back.
attached is our logo and our telephone number is 1300 48 92 16
the above are 2 essential elements to be included + our email address: admin@brightwellrs.com.au
also attached are our transparent price list

Target Market(s)
property investors,
people that manage properties themselves
Industry/Entity Type
Property Management
- arial
Look and feel

```html
<!DOCTYPE html>
<html lang="en">
<head>
<meta charset="utf-8">
<title>brightwell – Property Management DL Card</title>
<link rel="stylesheet" href="https://fonts.googleapis.com/css2?family=Arimo:wght@400;700&display=swap">
<style>
  :root {
    --backdrop: #e9e7e4;
    --card: #ffffff;
    --card-shade: #f1f1f1;
    --ink: #111111;
    --logo-ink: #2b2b2b;
    --muted: #b9b9b9;
    --ring: #6c6c6c;
    --photo-light: #efe6d6;
    --photo-mid: #c9b595;
    --photo-dark: #6e5c45;
  }
  * { box-sizing: border-box; margin: 0; padding: 0; }
  html, body {
    width: 1200px;
    height: 900px;
    overflow: hidden;
    background: var(--backdrop);
    font-family: "Arimo", Arial, sans-serif;
    color: var(--ink);
  }
  .canvas { position: relative; width: 1200px; height: 900px; }

  .card {
    position: absolute;
    background: linear-gradient(135deg, var(--card) 0%, var(--card-shade) 50%, var(--card) 100%);
    overflow: hidden;
    box-shadow: 0 3px 10px rgba(0,0,0,0.18);
  }
  .card--front { left: 14px; top: 0; width: 1006px; height: 440px; }
  .card--back  { left: 168px; top: 446px; width: 1009px; height: 445px; }

  .photo {
    position: absolute;
    border-radius: 50%;
    border: 3px solid var(--ring);
    background: radial-gradient(circle at 40% 35%, var(--photo-light) 0%, var(--photo-mid) 55%, var(--photo-dark) 100%);
  }
  .photo--large { width: 376px; height: 376px; }
  .photo--small { width: 222px; height: 222px; }

  .brand {
    position: absolute;
    font-weight: 400;
    font-size: 56px;
    letter-spacing: -0.5px;
    color: var(--logo-ink);
    line-height: 1;
    white-space: nowrap;
  }
  .headline {
    position: absolute;
    font-weight: 700;
    white-space: nowrap;
    line-height: 1;
  }
  .call-label {
    position: absolute;
    font-weight: 700;
    font-size: 23px;
    color: var(--muted);
    white-space: nowrap;
    transform: translateX(-50%);
    line-height: 1;
  }
  .phone {
    position: absolute;
    font-weight: 700;
    font-size: 35px;
    white-space: nowrap;
    transform: translateX(-50%);
    line-height: 1;
    letter-spacing: 0.5px;
  }
  .footer-link {
    position: absolute;
    font-size: 16px;
    white-space: nowrap;
    line-height: 1;
  }

  /* front */
  .card--front .photo--large { left: 7px; top: -6px; }
  .card--front .photo--small { left: 324px; top: 221px; }
  .card--front .brand { left: 620px; top: 30px; }
  .card--front .headline { left: 422px; top: 193px; font-size: 26px; }
  .card--front .call-label { left: 765px; top: 364px; }
  .card--front .phone { left: 756px; top: 396px; }

  /* back */
  .card--back .brand { left: 98px; top: 22px; }
  .card--back .headline { left: 8px; top: 171px; font-size: 33px; }
  .card--back .call-label { left: 263px; top: 270px; }
  .card--back .phone { left: 254px; top: 305px; }
  .card--back .photo--large { left: 615px; top: -6px; }
  .card--back .photo--small { left: 463px; top: 215px; }
  .card--back .footer-link--web { left: 11px; top: 416px; }
  .card--back .footer-link--mail { left: 270px; top: 416px; }
</style>
</head>
<body>
<main class="canvas">
  <section class="card card--front" aria-label="Card front">
    <div class="photo photo--large" role="img" aria-label="Photo of a bright open-plan living room with dining area and kitchen"></div>
    <div class="photo photo--small" role="img" aria-label="Photo of a light modern lounge with balcony doors"></div>
    <div class="brand">brightwell</div>
    <h1 class="headline">We Specialise In Property Management</h1>
    <p class="call-label">Cal Us Today:</p>
    <p class="phone">1300 48 92 16</p>
  </section>

  <section class="card card--back" aria-label="Card back">
    <div class="brand">brightwell</div>
    <h2 class="headline">Tailored to your Requirements</h2>
    <p class="call-label">Cal Us Today:</p>
    <p class="phone">1300 48 92 16</p>
    <div class="photo photo--large" role="img" aria-label="Photo of a bright open-plan living room with dining area and kitchen"></div>
    <div class="photo photo--small" role="img" aria-label="Photo of a light modern lounge with a glass dining table"></div>
    <p class="footer-link footer-link--web">www.brightwellrs.com.au</p>
    <p class="footer-link footer-link--mail">admin@brightwellrs.com.au</p>
  </section>
</main>
</body>
</html>
```